MRT Property - Business Cards

Looking for a business card & general letterhead, signage etc design for our new logo.

Colours:
000a20
0056a2
00b5ef
0088ce
68cef2

Fonts:
Poppins
Karla

Please keep look and feel of new brand - example in the zip package I sent.

```html
<!DOCTYPE html>
<html lang="en">
<head>
<meta charset="utf-8">
<title>MRT Property – Stationery</title>
<link href="https://fonts.googleapis.com/css2?family=Poppins:wght@500;600&family=Karla:wght@400;500&family=Montserrat:wght@300;400&display=swap" rel="stylesheet">
<style>
  :root {
    --navy: #000a20;
    --ink: #121629;
    --royal: #0056a2;
    --sky: #00b5ef;
    --ocean: #0088ce;
    --ice: #68cef2;
    --paper: #ffffff;
    --backdrop: #b4b4b4;
    --rule: #d4d4d4;
    --body-grey: #9a9a9a;
    --text-grey: #555555;
  }
  * { margin: 0; padding: 0; box-sizing: border-box; }
  html, body { width: 1200px; height: 1068px; overflow: hidden; background: var(--backdrop); }
  .canvas { position: relative; width: 1200px; height: 1068px; }

  /* Letterhead */
  .letterhead {
    position: absolute; left: 70px; top: 108px; width: 602px; height: 852px;
    background: var(--paper); overflow: hidden;
  }
  .brand-name {
    font-family: 'Poppins', sans-serif; font-weight: 600; color: var(--royal);
    display: flex; align-items: center; gap: 8px; white-space: nowrap;
  }
  .brand-name .brand-dot { width: 14px; height: 14px; border-radius: 50%; background: var(--sky); flex: none; }
  .letterhead .brand-name { position: absolute; left: 43px; top: 72px; font-size: 26px; }

  .contact-block {
    position: absolute; right: 40px; top: 48px;
    font-family: 'Karla', sans-serif; font-size: 9px; color: var(--text-grey);
    text-align: right; line-height: 1.05;
  }
  .contact-row { display: flex; justify-content: flex-end; align-items: center; gap: 4px; margin-bottom: 8px; }
  .contact-row.address { margin-bottom: 14px; }
  .icon { width: 11px; height: 11px; flex: none; display: block; }

  .header-rule { position: absolute; left: 43px; right: 44px; top: 153px; height: 1px; background: var(--rule); }

  .recipient { position: absolute; left: 43px; top: 218px; font-family: 'Montserrat', sans-serif; font-size: 11px; color: var(--text-grey); line-height: 1.25; }
  .recipient-name { font-family: 'Poppins', sans-serif; font-weight: 600; font-size: 16px; color: var(--royal); margin-bottom: 6px; letter-spacing: 0.2px; }
  .recipient p { margin-bottom: 6px; }
  .letter-date { position: absolute; right: 44px; top: 306px; font-family: 'Montserrat', sans-serif; font-size: 12px; color: var(--text-grey); }

  .letter-body { position: absolute; left: 44px; right: 43px; top: 338px; font-family: 'Montserrat', sans-serif; font-weight: 300; font-size: 12px; color: var(--body-grey); line-height: 18.7px; text-align: justify; }
  .letter-body p { margin-bottom: 18.7px; }

  .signature { position: absolute; left: 68px; top: 612px; width: 90px; height: 56px; background: linear-gradient(90deg, #e9e9e9, #f4f4f4); border-radius: 3px; }
  .signatory { position: absolute; left: 44px; top: 675px; font-family: 'Poppins', sans-serif; font-weight: 600; font-size: 16px; color: #111; }

  .footer-band { position: absolute; left: 0; right: 0; bottom: 0; height: 8px; }

  /* Business cards */
  .card { position: absolute; width: 300px; height: 182px; overflow: hidden; }
  .card-front { left: 790px; top: 284px; background: var(--ink); display: flex; align-items: center; justify-content: center; }
  .card-front .brand-name { color: var(--paper); font-size: 30px; }

  .card-back { left: 790px; top: 494px; background: var(--paper); }
  .card-accent { position: absolute; left: 0; top: 20px; width: 12px; height: 25px; background: var(--royal); }
  .card-holder { position: absolute; left: 21px; top: 18px; font-family: 'Poppins', sans-serif; font-weight: 500; font-size: 13px; color: var(--sky); white-space: nowrap; }
  .card-holder strong { font-weight: 600; color: var(--royal); }
  .card-role { position: absolute; left: 21px; top: 37px; font-family: 'Karla', sans-serif; font-size: 9px; color: var(--text-grey); }
  .card-contacts { position: absolute; left: 21px; top: 96px; font-family: 'Karla', sans-serif; font-size: 6.5px; color: var(--text-grey); line-height: 1.3; }
  .card-contacts .contact-row { justify-content: flex-start; align-items: flex-start; margin-bottom: 5px; gap: 3px; }
  .card-contacts .contact-row.address { margin-bottom: 8px; }
  .card-contacts .icon { width: 8px; height: 8px; }
  .card-back .footer-band { height: 4px; }
</style>
</head>
<body>
<svg width="0" height="0" style="position:absolute">
  <defs>
    <symbol id="icon-pin" viewBox="0 0 12 12"><rect width="12" height="12" rx="1.5" fill="#0056a2"/><path d="M6 2.2a2.6 2.6 0 0 0-2.6 2.6C3.4 6.8 6 9.8 6 9.8s2.6-3 2.6-5A2.6 2.6 0 0 0 6 2.2z" fill="#fff"/><circle cx="6" cy="4.8" r="1" fill="#0056a2"/></symbol>
    <symbol id="icon-phone" viewBox="0 0 12 12"><rect width="12" height="12" rx="1.5" fill="#00b5ef"/><path d="M3.2 2.6l1.4-.2.8 1.9-.9.7a5 5 0 0 0 2.5 2.5l.7-.9 1.9.8-.2 1.4C6 9 3 6 3.2 2.6z" fill="#fff"/></symbol>
    <symbol id="icon-mail" viewBox="0 0 12 12"><rect width="12" height="12" rx="1.5" fill="#00b5ef"/><rect x="2.4" y="3.4" width="7.2" height="5.2" fill="none" stroke="#fff" stroke-width=".9"/><path d="M2.4 3.4L6 6.4l3.6-3" fill="none" stroke="#fff" stroke-width=".9"/></symbol>
    <symbol id="icon-web" viewBox="0 0 12 12"><rect width="12" height="12" rx="1.5" fill="#00b5ef"/><path d="M4 2.5v6.6l1.6-1.5 1.2 2.4 1-.5-1.2-2.3 2.1-.2z" fill="#fff"/></symbol>
    <linearGradient id="band" x1="0" x2="1">
      <stop offset="0" stop-color="#00b5ef"/>
    </linearGradient>
  </defs>
</svg>

<main class="canvas">
  <section class="letterhead">
    <div class="brand-name"><span class="brand-dot"></span>MRT Property</div>

    <div class="contact-block">
      <div class="contact-row address"><span>210 Harbor Crest Avenue<br>Fairview, ST 40120</span><svg class="icon"><use href="#icon-pin"/></svg></div>
      <div class="contact-row"><span>+00 987 654 32</span><svg class="icon"><use href="#icon-phone"/></svg></div>
      <div class="contact-row"><span>hello@mrtproperty.com</span><svg class="icon"><use href="#icon-mail"/></svg></div>
      <div class="contact-row"><span>www.mrtproperty.com</span><svg class="icon"><use href="#icon-web"/></svg></div>
    </div>

    <div class="header-rule"></div>

    <div class="recipient">
      <h2 class="recipient-name">DANA HOLLIS</h2>
      <p>0987-654-321</p>
      <p>dana@mrtproperty.com</p>
      <p>58 Linden Row Suite<br>4 Maple Grove, ST 0000</p>
    </div>
    <div class="letter-date">12 March 2024</div>

    <div class="letter-body">
      <p>Lorem ipsum dolor sit amet, consectetuer adipiscing elit, sed diam nonummy nibh euismod tincidunt ut laoreet dolore magna aliquam erat volutpat. Ut wisi enim ad minim veniam, quis nostrud exerci tation ullamcorper suscipit lobortis nisl ut aliquip ex ea commodo consequat. Duis autem vel eum iriure dolor in hendrerit in vulputate velit esse molestie consequat, vel illum dolore eu feugiat nulla facilisis at vero eros et accumsan et iusto odio dignissim qui blandit praesent luptatum zzril delenit augue duis dolore te feugait nulla facilisi.</p>
      <p>Lorem ipsum dolor sit amet, cons ectetuer adipiscing elit, sed diam nonummy nibh euismod tincidunt ut laoreet dolore magna aliquam erat volutpat. Ut wisi enim ad minim veniam, quis nostrud exerci tation ullamcorper suscipit lobortis nisl ut aliquip ex ea commodo consequat.</p>
    </div>

    <div class="signature" role="img" aria-label="Handwritten signature of Dana Hollis"></div>
    <div class="signatory">Ms. Dana Hollis</div>

    <svg class="footer-band" viewBox="0 0 602 8" preserveAspectRatio="none">
      <polygon points="0,0 430,0 445,8 0,8" fill="#00b5ef"/>
      <polygon points="530,0 602,0 602,8 538,8" fill="#121629"/>
    </svg>
  </section>

  <section class="card card-front">
    <div class="brand-name"><span class="brand-dot"></span>MRT Property</div>
  </section>

  <section class="card card-back">
    <div class="card-accent"></div>
    <h3 class="card-holder">MARCUS T. <strong>REED</strong></h3>
    <div class="card-role">Managing Director</div>
    <div class="card-contacts">
      <div class="contact-row address"><svg class="icon"><use href="#icon-pin"/></svg><span>210 Harbor Crest Avenue<br>Fairview, ST 40120</span></div>
      <div class="contact-row"><svg class="icon"><use href="#icon-phone"/></svg><span>+00 987 654 32</span></div>
      <div class="contact-row"><svg class="icon"><use href="#icon-mail"/></svg><span>hello@mrtproperty.com</span></div>
      <div class="contact-row"><svg class="icon"><use href="#icon-web"/></svg><span>www.mrtproperty.com</span></div>
    </div>
    <svg class="footer-band" viewBox="0 0 300 4" preserveAspectRatio="none">
      <polygon points="0,0 188,0 196,4 0,4" fill="#00b5ef"/>
      <polygon points="250,0 300,0 300,4 254,4" fill="#121629"/>
    </svg>
  </section>
</main>
</body>
</html>
```